Frostvale Harborline LLC

we need a business card design

Industry/Entity Type

hvac

Contact Information for Business Card

my logo

Requirements
Must have
• my logo and same colors

```html
<!DOCTYPE html>
<html lang="en">
<head>
<meta charset="utf-8">
<title>Frostvale Harborline LLC – Business Card</title>
<link rel="stylesheet" href="https://fonts.googleapis.com/css2?family=Lato:wght@400;700&display=swap">
<style>
  :root {
    --bg: #3a3a3c;
    --brand-blue: #03508f;
    --wave-blue: #0a5fac;
    --name-blue: #1a4fe0;
    --accent-yellow: #f6b94d;
    --paper: #ffffff;
    --ink: #1c1c1c;
  }
  * { box-sizing: border-box; margin: 0; padding: 0; }
  html, body { width: 1200px; height: 875px; overflow: hidden; }
  body {
    background: var(--bg);
    font-family: "Lato", Arial, sans-serif;
    display: flex;
    flex-direction: column;
    align-items: center;
    justify-content: center;
    gap: 60px;
  }
  .card {
    position: relative;
    width: 560px;
    height: 320px;
    border-radius: 22px;
    overflow: hidden;
    box-shadow: 0 10px 30px rgba(0,0,0,.35);
  }
  .card--back {
    background: var(--brand-blue);
    display: flex;
    align-items: center;
    justify-content: center;
  }
  .wordmark {
    display: flex;
    align-items: center;
    gap: 12px;
    font-weight: 700;
    font-size: 28px;
    line-height: 1.15;
  }
  .wordmark__dot {
    width: 18px; height: 18px; border-radius: 50%;
    flex: none;
  }
  .card--back .wordmark { color: var(--paper); }
  .card--back .wordmark__dot { background: var(--accent-yellow); }

  .card--front { background: var(--paper); }
  .card__waves { position: absolute; inset: 0; }
  .card__tab {
    position: absolute; top: 18px; right: 30px;
    width: 14px; height: 30px; background: var(--brand-blue);
  }
  .card--front .wordmark {
    position: absolute; left: 40px; top: 110px;
    color: var(--brand-blue); font-size: 24px; width: 220px;
  }
  .card--front .wordmark__dot { background: var(--brand-blue); }
  .person {
    position: absolute; top: 26px; right: 60px; text-align: right;
  }
  .person__name { color: var(--name-blue); font-size: 24px; font-weight: 400; line-height: 1.2; }
  .person__role { color: var(--ink); font-size: 13px; margin-top: 1px; }
  .contact {
    position: absolute; right: 26px; bottom: 34px;
    list-style: none; text-align: right;
    color: var(--paper); font-size: 12.5px; line-height: 1.5;
  }
  .contact li { display: flex; align-items: center; justify-content: flex-end; gap: 8px; }
  .contact svg { width: 13px; height: 13px; fill: var(--paper); flex: none; }
  .contact .no-icon { padding-right: 21px; }
</style>
</head>
<body>

  <section class="card card--back" aria-label="Card back">
    <div class="wordmark"><span class="wordmark__dot"></span><span>Frostvale Harborline LLC</span></div>
  </section>

  <section class="card card--front" aria-label="Card front">
    <svg class="card__waves" viewBox="0 0 560 320" aria-hidden="true">
      <path d="M0 290 C120 300 230 270 300 180 C260 260 150 305 0 308 Z" fill="var(--accent-yellow)"/>
      <path d="M470 92 C410 115 370 160 340 210 C305 268 260 305 180 318" fill="none" stroke="var(--wave-blue)" stroke-width="6"/>
      <path d="M560 80 C460 95 400 130 360 190 C320 250 280 300 200 320 L560 320 Z" fill="var(--wave-blue)"/>
      <path d="M0 304 L560 304 L560 320 L0 320 Z" fill="var(--wave-blue)"/>
    </svg>
    <span class="card__tab"></span>

    <div class="wordmark"><span class="wordmark__dot"></span><span>Frostvale Harborline LLC</span></div>

    <div class="person">
      <p class="person__name">Marcus Ellery</p>
      <p class="person__role">Owner</p>
    </div>

    <ul class="contact">
      <li>044-123 456 789
        <svg viewBox="0 0 24 24"><path d="M6.6 10.8a15 15 0 0 0 6.6 6.6l2.2-2.2c.3-.3.7-.4 1-.2 1.1.4 2.3.6 3.6.6.6 0 1 .4 1 1V20c0 .6-.4 1-1 1A17 17 0 0 1 3 4c0-.6.4-1 1-1h3.5c.6 0 1 .4 1 1 0 1.3.2 2.5.6 3.6.1.3 0 .7-.2 1z"/></svg></li>
      <li>info@frostvaleharbor.com
        <svg viewBox="0 0 24 24"><path d="M2 5h20v14H2z M3 6l9 7 9-7" fill="none" stroke="#fff" stroke-width="2"/></svg></li>
      <li>www.frostvaleharbor.com
        <svg viewBox="0 0 24 24"><circle cx="12" cy="12" r="9" fill="none" stroke="#fff" stroke-width="2"/><path d="M3 12h18M12 3c3 3 3 15 0 18M12 3c-3 3-3 15 0 18" fill="none" stroke="#fff" stroke-width="1.6"/></svg></li>
      <li>421, Address line goes here
        <svg viewBox="0 0 24 24"><path d="M12 2a7 7 0 0 0-7 7c0 5 7 13 7 13s7-8 7-13a7 7 0 0 0-7-7zm0 9.5a2.5 2.5 0 1 1 0-5 2.5 2.5 0 0 1 0 5z"/></svg></li>
      <li class="no-icon">45452, Country name</li>
    </ul>
  </section>

</body>
</html>
```